Quillmarsh Property Solutions need a business card design

Hello guys. We would need a business card design asap please.
We are a start up property investment business based in London UK specialised in buying, selling, managing and letting properties and helping distressed property owners.
The name of our Business is Quillmarsh, the logo symbolises the four fundamental elements of the world (earth, air, fire and water) and so it stands for strength, stability, longevity.
We would like the business card to communicate professionalism and reliability. Many many thanks indeed for your work.

Details:

1.) Rosalind Updike
Property Investor
Mobile: +44(0)7700123456
Email: rosalind.quillmarsh@mailbox-example.com

2.) Dominic Updike
Property Investor
Mobile: +44(0)7700987654
Email: dominic.quillmarsh@mailbox-example.com

```html
<!DOCTYPE html>
<html lang="en">
<head>
<meta charset="utf-8">
<title>Quillmarsh Property Solutions – Business Card</title>
<link rel="stylesheet" href="https://fonts.googleapis.com/css2?family=Open+Sans:wght@400;600;700;800&display=swap">
<style>
  :root {
    --bg: #e6e7ee;
    --card: #ffffff;
    --green: #0b5a30;
    --red: #c8242e;
    --ink: #1c1c1c;
    --grey: #4a4a4a;
    --rule: #9a9a9a;
  }
  * { box-sizing: border-box; margin: 0; padding: 0; }
  html, body { width: 1200px; height: 987px; overflow: hidden; }
  body {
    background: var(--bg);
    font-family: "Open Sans", Arial, sans-serif;
    position: relative;
  }
  .card {
    position: absolute;
    top: 328px;
    width: 560px;
    height: 330px;
    border-radius: 22px;
    overflow: hidden;
    box-shadow: 0 6px 18px rgba(0,0,0,0.12);
  }
  .card--front { left: 30px; background: var(--card); }
  .card--back  { left: 610px; background: var(--green); }

  .brand {
    position: absolute;
    left: 40px;
    top: 56px;
    width: 180px;
    display: flex;
    flex-direction: column;
    align-items: flex-start;
  }
  .brand__mark { width: 40px; height: 40px; background: var(--green); margin: 0 0 12px 70px; }
  .brand__name {
    font-weight: 800;
    font-size: 22px;
    letter-spacing: 1px;
    color: var(--ink);
    line-height: 1;
    white-space: nowrap;
  }
  .brand__tagline {
    font-weight: 800;
    font-size: 9px;
    letter-spacing: 1px;
    color: var(--ink);
    margin-top: 5px;
    white-space: nowrap;
  }

  .divider {
    position: absolute;
    left: 236px;
    top: 78px;
    width: 1px;
    height: 110px;
    background: linear-gradient(to bottom, transparent, var(--rule) 45%, transparent);
  }
  .contact {
    position: absolute;
    left: 254px;
    top: 108px;
    list-style: none;
    color: var(--grey);
    font-size: 12.5px;
  }
  .contact__item { display: flex; align-items: center; gap: 8px; margin-bottom: 18px; white-space: nowrap; }
  .contact__icon { width: 14px; height: 14px; flex: none; }

  .rule-red {
    position: absolute;
    left: 0; right: 0;
    height: 1px;
    background: var(--red);
  }
  .rule-red--top { top: 208px; }
  .rule-red--bottom { top: 300px; }
  .name-band {
    position: absolute;
    left: 0; right: 0;
    top: 216px;
    height: 76px;
    background: var(--green);
    color: #fff;
    display: flex;
    align-items: center;
    padding-left: 112px;
    font-size: 20px;
    white-space: nowrap;
  }
  .name-band__name { font-weight: 600; text-transform: uppercase; margin-right: 7px; }
  .name-band__role { font-weight: 400; }

  .back-brand {
    position: absolute;
    inset: 0;
    display: flex;
    align-items: center;
    justify-content: center;
    gap: 16px;
  }
  .back-brand__mark { width: 40px; height: 40px; background: #ffffff; }
  .back-brand__name {
    font-weight: 800;
    font-size: 40px;
    letter-spacing: 2px;
    color: #ffffff;
  }
</style>
</head>
<body>
  <section class="card card--front" aria-label="Business card front">
    <div class="brand">
      <div class="brand__mark"></div>
      <div class="brand__name">QUILLMARSH</div>
      <div class="brand__tagline">PROPERTY SOLUTIONS</div>
    </div>

    <div class="divider"></div>

    <ul class="contact">
      <li class="contact__item">
        <svg class="contact__icon" viewBox="0 0 14 14" aria-hidden="true">
          <rect x="3" y="0.5" width="8" height="13" rx="1.5" fill="none" stroke="#4a4a4a" stroke-width="1.2"/>
          <rect x="4.5" y="2.5" width="5" height="4" fill="#4a4a4a"/>
          <circle cx="5.5" cy="9" r="0.7" fill="#4a4a4a"/><circle cx="8.5" cy="9" r="0.7" fill="#4a4a4a"/>
          <circle cx="5.5" cy="11.2" r="0.7" fill="#4a4a4a"/><circle cx="8.5" cy="11.2" r="0.7" fill="#4a4a4a"/>
        </svg>
        <span>+44(0)7700987654</span>
      </li>
      <li class="contact__item">
        <svg class="contact__icon" viewBox="0 0 14 14" aria-hidden="true">
          <rect x="0.8" y="3" width="12.4" height="9" rx="1" fill="none" stroke="#4a4a4a" stroke-width="1.2"/>
          <path d="M1 3.5 L7 8 L13 3.5" fill="none" stroke="#4a4a4a" stroke-width="1.2"/>
        </svg>
        <span>dominic.quillmarsh@mailbox-example.com</span>
      </li>
    </ul>

    <div class="rule-red rule-red--top"></div>
    <div class="name-band">
      <span class="name-band__name">Dominic Updike,</span>
      <span class="name-band__role">Property Investor</span>
    </div>
    <div class="rule-red rule-red--bottom"></div>
  </section>

  <section class="card card--back" aria-label="Business card back">
    <div class="back-brand">
      <div class="back-brand__mark"></div>
      <div class="back-brand__name">QUILLMARSH</div>
    </div>
  </section>
</body>
</html>
```